LDI Illustration Web Design

Create illustration web design company for Lumaviro Darsa Informatika (LDI). I more prefer design with illustration concept. Detail for requirement please see attach file. I'm also attach LDI logo. This logo had 2 type, 2D design and 3D design. You can chose one of them, or used both.
For the winner or had good design would be possible to private project to completeness this website
Attach file requirement is guidance for design, but any changes are welcome
Updates
Sorry, I forgot about contact. Please add menu contact. You can put this menu besides login menu or part of menu level #1, or put on some where to adjust your design. Menu contact will give pop up window to email LDI Company and Company Information (Address, Telephone, etc)
Target Market(s)
Company (Business To Business)
Industry/Entity Type
It Company
Look and feel
Each slider illustrates characteristics of the customer's brand and the style your logo design should communicate.

```html
<!DOCTYPE html>
<html lang="en">
<head>
<meta charset="UTF-8">
<title>Lumaviro Darsa Informatika – Software Developer and IT Solution Consultant</title>
<link rel="stylesheet" href="https://fonts.googleapis.com/css2?family=PT+Sans:wght@400;700&family=Roboto+Condensed:wght@700&display=swap">
<style>
  :root {
    --sky-light: #f4f9fd;
    --sky-mid: #cfe4f5;
    --sky-deep: #8fc0e8;
    --cloud: #ffffff;
    --cloud-blue: #b9d8f1;
    --planet-core: #5a9e1c;
    --planet-mid: #8cc63f;
    --planet-edge: #c4e26a;
    --bubble-top: #1b6f9c;
    --bubble-bottom: #0b3e62;
    --bubble-ring: #ffffff;
    --ink: #1d2f45;
    --login-top: #8ed12a;
    --login-bottom: #4f9a0e;
    --footer-bg: #0f2c3e;
    --footer-text: #b8c6d0;
    --logo-green: #6aab2a;
  }
  * { margin: 0; padding: 0; box-sizing: border-box; }
  html, body { width: 1200px; height: 844px; overflow: hidden; }
  body {
    position: relative;
    font-family: "PT Sans", sans-serif;
    background: radial-gradient(ellipse 70% 80% at 50% 45%, var(--sky-light) 0%, var(--sky-mid) 70%, var(--sky-deep) 100%);
  }
  .site-header .brand {
    position: absolute; left: 52px; top: 40px;
    display: flex; align-items: center; gap: 14px;
    text-decoration: none;
  }
  .brand-mark {
    width: 58px; height: 58px; border-radius: 50%;
    background: var(--logo-green);
  }
  .brand-name {
    font-family: "PT Sans", sans-serif;
    font-weight: 700; font-size: 56px; line-height: 1;
    color: var(--logo-green); letter-spacing: 2px;
  }
  .login-button {
    position: absolute; left: 1025px; top: 37px;
    width: 113px; height: 44px; border-radius: 22px;
    border: 2px solid #ffffff;
    background: linear-gradient(var(--login-top), var(--login-bottom));
    color: #fff; font-family: "Roboto Condensed", sans-serif;
    font-weight: 700; font-size: 19px;
    display: flex; align-items: center; justify-content: center;
    text-decoration: none;
    box-shadow: 0 1px 3px rgba(0,0,0,.25);
  }
  .hero-illustration {
    position: absolute; left: 180px; top: 34px;
    width: 876px; height: 746px;
    border-radius: 48% 48% 44% 44%;
    background:
      radial-gradient(circle 212px at 49% 63%, var(--planet-core) 0%, var(--planet-mid) 65%, var(--planet-edge) 92%, rgba(196,226,106,0) 100%),
      radial-gradient(ellipse 50% 50% at 50% 50%, var(--cloud) 55%, var(--cloud-blue) 85%, rgba(185,216,241,0) 100%);
  }
  .main-nav { position: absolute; inset: 0; pointer-events: none; }
  .main-nav svg { width: 1200px; height: 844px; display: block; }
  .nav-label {
    font-family: "Roboto Condensed", sans-serif;
    font-weight: 700; fill: #ffffff;
  }
  .intro-panel {
    position: absolute; left: 0; top: 386px;
    width: 484px; height: 231px;
    background: rgba(255,255,255,.72);
    clip-path: polygon(0 0, 100% 0, 85% 100%, 0 100%);
    padding: 30px 0 0 57px;
  }
  .intro-title {
    font-weight: 700; font-size: 40px; line-height: 1.05;
    color: var(--ink);
  }
  .intro-subtitle {
    font-weight: 700; font-size: 28px; line-height: 1.3;
    color: var(--ink); margin-top: 4px;
  }
  .intro-text {
    margin-top: 10px; width: 360px;
    font-size: 14px; line-height: 22px; color: var(--ink);
  }
  .site-footer {
    position: absolute; left: 0; top: 780px;
    width: 1200px; height: 64px;
    background: var(--footer-bg);
    display: flex; align-items: center; justify-content: space-between;
    padding: 0 56px 0 53px;
  }
  .copyright { font-size: 13px; color: var(--footer-text); }
  .social-links { display: flex; gap: 7px; list-style: none; }
  .social-links li {
    width: 27px; height: 27px; border-radius: 50%; background: #ffffff;
  }
</style>
</head>
<body>
  <header class="site-header">
    <a class="brand" href="#">
      <span class="brand-mark"></span>
      <span class="brand-name">LDI</span>
    </a>
    <a class="login-button" href="#">Login</a>
  </header>

  <div class="hero-illustration" role="img" aria-label="Illustration of a small grassy green planet with trees and a bird, surrounded by soft white and blue clouds"></div>

  <nav class="main-nav" aria-label="Main menu">
    <svg viewBox="0 0 1200 844" xmlns="http://www.w3.org/2000/svg">
      <defs>
        <linearGradient id="bubbleFill" x1="0" y1="0" x2="0" y2="1">
          <stop offset="0" stop-color="var(--bubble-top)"/>
          <stop offset="1" stop-color="var(--bubble-bottom)"/>
        </linearGradient>
      </defs>
      <g class="nav-bubble">
        <path d="M400 318 L452 348 L418 300 Z" fill="#fff"/>
        <circle cx="366" cy="277" r="66" fill="var(--bubble-ring)"/>
        <circle cx="366" cy="277" r="59" fill="url(#bubbleFill)"/>
        <text class="nav-label" x="366" y="284" font-size="22" text-anchor="middle">Company</text>
      </g>
      <g class="nav-bubble">
        <path d="M548 252 L568 288 L572 248 Z" fill="#fff"/>
        <circle cx="535" cy="198" r="67" fill="var(--bubble-ring)"/>
        <circle cx="535" cy="198" r="60" fill="url(#bubbleFill)"/>
        <text class="nav-label" x="535" y="206" font-size="22" text-anchor="middle">Services</text>
      </g>
      <g class="nav-bubble">
        <path d="M700 246 L692 286 L728 252 Z" fill="#fff"/>
        <circle cx="722" cy="204" r="57" fill="var(--bubble-ring)"/>
        <circle cx="722" cy="204" r="50" fill="url(#bubbleFill)"/>
        <text class="nav-label" x="722" y="212" font-size="21" text-anchor="middle">Clients</text>
      </g>
      <g class="nav-bubble">
        <path d="M822 326 L778 352 L838 336 Z" fill="#fff"/>
        <circle cx="862" cy="285" r="66" fill="var(--bubble-ring)"/>
        <circle cx="862" cy="285" r="59" fill="url(#bubbleFill)"/>
        <text class="nav-label" x="862" y="292" font-size="22" text-anchor="middle">Product</text>
      </g>
      <g class="nav-bubble">
        <path d="M904 452 L872 470 L918 462 Z" fill="#fff"/>
        <circle cx="940" cy="417" r="56" fill="var(--bubble-ring)"/>
        <circle cx="940" cy="417" r="49" fill="url(#bubbleFill)"/>
        <text class="nav-label" x="940" y="425" font-size="22" text-anchor="middle">Blog</text>
      </g>
    </svg>
  </nav>

  <section class="intro-panel">
    <h1 class="intro-title">Software Developer</h1>
    <h2 class="intro-subtitle">and IT Solution Consultant</h2>
    <p class="intro-text">Duis tincidunt lectus quis dui viverra vestibulum. Suspendisse vulputate aliquam dui. Nulla elementum dui ut augue. Aliquam vehicula mi at mauris.</p>
  </section>

  <footer class="site-footer">
    <p class="copyright">© 2012 Company Name.&nbsp; All right reserved.&nbsp; Term of Use</p>
    <ul class="social-links">
      <li aria-label="Social link"></li>
      <li aria-label="Social link"></li>
      <li aria-label="Social link"></li>
      <li aria-label="Social link"></li>
    </ul>
  </footer>
</body>
</html>
```